Business card design needed

Card needs to say

Maren Heathwold
Investor - Solutions - Development

My business is in property deals. I would like the words above to be on the card. I have attached a logo for you to copy/recreate.
On the back you could list the following:

Creative property solutions

Thankyou, Maren

Target Market(s)

people wanting to get into the property market, desperate sellers, Mums & Dads wanting to help their kids to purchase a property. People who want to create wealth. People who are stuck and need a solution.

Industry/Entity Type

Business

Contact Information for Business Card

T: 0431 274 506
F: (07) 3842 1739
E: maren47@vbx-mail.com.au

Requirements
Must have
• Simple and effective.
Look like I am here to help
Should not have
• Should not look like a realestate agent

```html
<!DOCTYPE html>
<html lang="en">
<head>
<meta charset="utf-8">
<title>Maren Heathwold – Business Card</title>
<link rel="stylesheet" href="https://fonts.googleapis.com/css2?family=Arimo:wght@400;700&display=swap">
<style>
  :root {
    --backdrop: #e4e4e2;
    --card-dark: #2b2828;
    --card-light: #fbfbfb;
    --brand-green: #7bb741;
    --text-grey: #5c5c5c;
    --text-grey-soft: #8d8b8b;
  }
  * { box-sizing: border-box; margin: 0; padding: 0; }
  html, body {
    width: 1200px;
    height: 800px;
    overflow: hidden;
    background: var(--backdrop);
    font-family: "Arimo", Arial, sans-serif;
  }
  .sheet {
    width: 1200px;
    height: 800px;
    display: flex;
    align-items: center;
    justify-content: center;
    gap: 60px;
  }
  .card {
    width: 525px;
    height: 300px;
    position: relative;
    box-shadow: 0 6px 18px rgba(0,0,0,.18);
  }

  /* Front */
  .card--front {
    background: var(--card-dark);
    display: flex;
    flex-direction: column;
    align-items: center;
    justify-content: center;
    text-align: center;
  }
  .brand-name {
    display: flex;
    align-items: center;
    gap: 10px;
    color: var(--brand-green);
    font-weight: 700;
    font-size: 38px;
    letter-spacing: -0.5px;
    line-height: 1;
  }
  .brand-square {
    width: 14px;
    height: 14px;
    background: var(--brand-green);
  }
  .front-services {
    margin-top: 8px;
    color: var(--text-grey-soft);
    font-weight: 700;
    font-size: 14px;
    line-height: 1.2;
  }

  /* Back */
  .card--back {
    background: var(--card-light);
  }
  .back-block {
    position: absolute;
    right: 34px;
    bottom: 40px;
    text-align: left;
  }
  .back-name {
    color: var(--brand-green);
    font-weight: 700;
    font-size: 33px;
    letter-spacing: -0.5px;
    line-height: 1;
  }
  .back-tagline {
    margin-left: 78px;
    color: var(--text-grey);
    font-weight: 700;
    font-size: 15px;
    line-height: 1.2;
  }
  .contact {
    margin-top: 16px;
    margin-left: 60px;
    color: var(--text-grey);
    font-weight: 700;
    font-size: 14px;
    line-height: 1.45;
  }
  .contact .label { color: var(--brand-green); }
  .contact .email-line { margin-left: 72px; }
</style>
</head>
<body>
  <main class="sheet">
    <section class="card card--front" aria-label="Card front">
      <div class="brand-name"><span class="brand-square"></span>Maren Heathwold</div>
      <p class="front-services">Investments - Solutions - Developments<br>House &amp; Land Packages</p>
    </section>

    <section class="card card--back" aria-label="Card back">
      <div class="back-block">
        <div class="back-name">Maren Heathwold</div>
        <p class="back-tagline">Creative property solutions</p>
        <div class="contact">
          <p><span class="label">T:</span> 0431 274 506 <span class="label">F:</span> (07) 3842 1739</p>
          <p class="email-line"><span class="label">E:</span> maren47@vbx-mail.com.au</p>
        </div>
      </div>
    </section>
  </main>
</body>
</html>
```